Business Card design which attached logo. Company is called Crestline Shield and main colours are Orange & Black.

Company specialises in Paint Protection and Detailing for supercars.

Details needed on business card:

Sales

Address: Unit 14, 517 Hadley Road, Fernvale Heights, NSW 2200

Phone: 02 6194 2738

website: www.crestlineshield.com.au

Email: sales@crestlineshield.com.au

```html
<!DOCTYPE html>
<html lang="en">
<head>
<meta charset="UTF-8">
<title>Crestline Shield – Business Card</title>
<link href="https://fonts.googleapis.com/css2?family=Raleway:wght@300;400&display=swap" rel="stylesheet">
<style>
  :root {
    --backdrop: #2b2e33;
    --card-black: #0a0a0b;
    --card-white: #ffffff;
    --orange: #e8562a;
    --text-grey: #555a60;
    --faint-grey: #26282b;
  }
  * { margin: 0; padding: 0; box-sizing: border-box; }
  html, body {
    width: 1200px; height: 900px; overflow: hidden;
    background: var(--backdrop);
    font-family: "Raleway", sans-serif;
  }
  .sheet {
    width: 1200px; height: 900px;
    display: flex; flex-direction: column;
    align-items: center; justify-content: center; gap: 56px;
  }
  .card {
    position: relative;
    width: 620px; height: 354px;
    overflow: hidden;
    box-shadow: 0 12px 30px rgba(0,0,0,0.45);
  }

  /* Front */
  .card-front { background: var(--card-white); }
  .front-dark {
    position: absolute; left: 0; top: 0; width: 100%; height: 205px;
    background: var(--card-black);
  }
  .front-rule {
    position: absolute; left: 0; top: 212px; width: 100%; height: 3px;
    background: var(--card-black);
  }
  .brand {
    position: absolute; left: 44px; top: 30px; width: 210px;
  }
  .brand-illustration {
    width: 210px; height: 100px;
    background: linear-gradient(135deg, #1a0f0b 0%, #3a1a10 55%, #1a0f0b 100%);
    border-radius: 4px;
  }
  .brand-name {
    margin-top: 14px;
    color: var(--orange);
    font-weight: 300; font-size: 17px; letter-spacing: 1.5px;
    text-transform: uppercase; text-align: center;
  }
  .address {
    position: absolute; left: 32px; top: 232px;
    color: var(--orange);
    font-weight: 300; font-size: 13px; line-height: 18px;
  }
  .contact {
    position: absolute; right: 28px; top: 226px;
    text-align: right;
  }
  .person-name {
    color: var(--orange);
    font-weight: 300; font-size: 30px; letter-spacing: 2px;
    text-transform: uppercase; line-height: 36px;
    margin-bottom: 6px;
  }
  .contact-line {
    display: flex; justify-content: flex-end; align-items: center; gap: 8px;
    color: var(--text-grey);
    font-weight: 300; font-size: 15px; line-height: 22px;
  }
  .contact-line svg { width: 13px; height: 13px; fill: var(--orange); flex: none; }

  /* Back */
  .card-back {
    background: var(--card-black);
    display: flex; align-items: center; justify-content: center; gap: 12px;
  }
  .back-ring {
    position: absolute; left: 50%; top: 50%;
    width: 300px; height: 300px; margin: -150px 0 0 -150px;
    border: 3px solid var(--faint-grey); border-radius: 50%;
  }
  .back-dot {
    width: 16px; height: 16px; border-radius: 50%;
    border: 1.5px solid var(--orange);
    position: relative;
  }
  .back-name {
    position: relative;
    color: var(--orange);
    font-weight: 300; font-size: 14px; letter-spacing: 2px;
    text-transform: uppercase;
  }
</style>
</head>
<body>
<main class="sheet">

  <section class="card card-front">
    <div class="front-dark"></div>
    <div class="front-rule"></div>

    <div class="brand">
      <div class="brand-illustration" role="img" aria-label="Orange line drawing of a supercar silhouette"></div>
      <div class="brand-name">Crestline Shield</div>
    </div>

    <p class="address">Unit 14, 517 Hadley Road<br>Fernvale Heights, NSW 2200</p>

    <div class="contact">
      <h1 class="person-name">Marcus Reid</h1>
      <p class="contact-line">02 6194 2738
        <svg viewBox="0 0 24 24" aria-hidden="true"><path d="M6.6 10.8a15.1 15.1 0 0 0 6.6 6.6l2.2-2.2c.3-.3.7-.4 1-.2 1.1.4 2.3.6 3.6.6.6 0 1 .4 1 1V20c0 .6-.4 1-1 1A17 17 0 0 1 3 4c0-.6.4-1 1-1h3.5c.6 0 1 .4 1 1 0 1.3.2 2.5.6 3.6.1.3 0 .7-.2 1z"/></svg>
      </p>
      <p class="contact-line">sales@crestlineshield.com.au
        <svg viewBox="0 0 24 24" aria-hidden="true"><path d="M2 5h20v14H2zm2 2v.5l8 5 8-5V7zm0 2.8V17h16V9.8l-8 5z"/></svg>
      </p>
      <p class="contact-line">www.crestlineshield.com.au
        <svg viewBox="0 0 24 24" aria-hidden="true"><path d="M12 2a10 10 0 1 0 0 20 10 10 0 0 0 0-20zm6.9 9h-3a15 15 0 0 0-1.3-5.6A8 8 0 0 1 18.9 11zM12 4.1c.9 1.2 1.8 3.5 1.9 6.9h-3.8c.1-3.4 1-5.7 1.9-6.9zM9.4 5.4A15 15 0 0 0 8.1 11h-3a8 8 0 0 1 4.3-5.6zM5.1 13h3a15 15 0 0 0 1.3 5.6A8 8 0 0 1 5.1 13zm6.9 6.9c-.9-1.2-1.8-3.5-1.9-6.9h3.8c-.1 3.4-1 5.7-1.9 6.9zm2.6-1.3a15 15 0 0 0 1.3-5.6h3a8 8 0 0 1-4.3 5.6z"/></svg>
      </p>
    </div>
  </section>

  <section class="card card-back">
    <div class="back-ring"></div>
    <span class="back-dot"></span>
    <span class="back-name">Crestline Shield</span>
  </section>

</main>
</body>
</html>
```